Concierge Healthcare Business Card Design and Logo

We need a logo and business card design for a new company called "Sound Haven". We will provide concierge audiological care, hearing aids, hearing exams, custom hearing protection etc to patients in the comfort of their homes and offices. We would like a sleek and modern design preferably with an Ear related logo.

Target Market(s)

People with hearing loss, Hunters, Musicians
My usual clientele are older individuals so usually 50+ years old

Industry/Entity Type

Health Care

Contact Information for Business Card

Celia Brandt, AuD
Audiologist
512-648-2917
soundhaven@mailvoro.com
www.soundhaven-vorel.com

Logo Text

Sound Haven

Number of Pages Required

3 page

```html
<!DOCTYPE html>
<html lang="en">
<head>
<meta charset="utf-8">
<title>Sound Haven Business Card</title>
<link rel="stylesheet" href="https://fonts.googleapis.com/css2?family=Montserrat:wght@400;600&display=swap">
<style>
  :root {
    --backdrop: #2b2b2b;
    --card: #000000;
    --accent: #1ea7e8;
    --ink: #ffffff;
  }
  * { margin: 0; padding: 0; box-sizing: border-box; }
  html, body { width: 1200px; height: 900px; overflow: hidden; }
  body {
    background: var(--backdrop);
    font-family: "Montserrat", sans-serif;
    color: var(--ink);
    position: relative;
  }
  .card {
    position: absolute;
    left: 300px;
    width: 600px;
    height: 343px;
    background: var(--card);
    overflow: hidden;
  }
  .card-front { top: 87px; }
  .card-back { top: 470px; }

  /* front */
  .front-brand {
    position: absolute;
    left: 0; right: 0; top: 120px;
    display: flex; align-items: center; justify-content: center; gap: 16px;
  }
  .brand-square { width: 52px; height: 52px; background: var(--accent); }
  .front-brand .brand-name {
    font-size: 40px; font-weight: 600; letter-spacing: 3px;
    text-transform: uppercase; color: var(--ink);
  }
  .front-web {
    position: absolute; left: 0; right: 0; top: 200px;
    text-align: center; font-size: 17px; font-weight: 400;
  }
  .front-web .domain { color: var(--accent); }

  /* back */
  .back-brand {
    position: absolute; left: 40px; top: 48px;
    display: flex; align-items: center; gap: 14px;
  }
  .back-brand .brand-square { width: 44px; height: 44px; }
  .back-brand .brand-name {
    font-size: 30px; font-weight: 600; letter-spacing: 3px;
    text-transform: uppercase; color: var(--accent);
  }
  .rule { position: absolute; height: 1.5px; background: var(--accent); }
  .rule-upper { left: 290px; right: 0; top: 176px; }
  .rule-lower { left: 0; width: 96px; top: 214px; }
  .holder-name {
    position: absolute; left: 90px; top: 162px;
    font-size: 20px; font-weight: 600; color: var(--accent);
  }
  .holder-title {
    position: absolute; left: 104px; top: 198px;
    font-size: 15px; font-weight: 400;
  }
  .contact-list {
    position: absolute; left: 108px; top: 228px;
    list-style: none;
  }
  .contact-list li {
    display: flex; align-items: center; gap: 10px;
    font-size: 15px; height: 26px;
  }
  .contact-list svg { width: 13px; height: 13px; fill: var(--accent); flex: none; }
</style>
</head>
<body>
  <section class="card card-front">
    <div class="front-brand">
      <span class="brand-square"></span>
      <span class="brand-name">Sound Haven</span>
    </div>
    <p class="front-web">www.<span class="domain">soundhaven-vorel</span>.com</p>
  </section>

  <section class="card card-back">
    <div class="back-brand">
      <span class="brand-square"></span>
      <span class="brand-name">Sound Haven</span>
    </div>
    <div class="rule rule-upper"></div>
    <p class="holder-name">Celia Brandt, AuD</p>
    <p class="holder-title">Audiologist</p>
    <div class="rule rule-lower"></div>
    <ul class="contact-list">
      <li>
        <svg viewBox="0 0 24 24"><path d="M6.6 10.8a15.1 15.1 0 0 0 6.6 6.6l2.2-2.2c.3-.3.7-.4 1-.2 1.1.4 2.3.6 3.6.6.6 0 1 .4 1 1V20c0 .6-.4 1-1 1C10.6 21 3 13.4 3 4c0-.6.4-1 1-1h3.5c.6 0 1 .4 1 1 0 1.3.2 2.5.6 3.6.1.3 0 .7-.2 1z"/></svg>
        <span>512-648-2917</span>
      </li>
      <li>
        <svg viewBox="0 0 24 24"><path d="M2 5h20v14H2zm2 2v.5l8 5 8-5V7zm0 2.8V17h16V9.8l-8 5z"/></svg>
        <span>soundhaven@mailvoro.com</span>
      </li>
      <li>
        <svg viewBox="0 0 24 24"><path d="M12 2a10 10 0 1 0 0 20 10 10 0 0 0 0-20zm6.9 9h-3a15 15 0 0 0-1.3-5.6A8 8 0 0 1 18.9 11zM12 4.1c.9 1.3 1.8 3.6 1.9 6.9h-3.8c.1-3.3 1-5.6 1.9-6.9zM9.4 5.4A15 15 0 0 0 8.1 11h-3a8 8 0 0 1 4.3-5.6zM5.1 13h3a15 15 0 0 0 1.3 5.6A8 8 0 0 1 5.1 13zm6.9 6.9c-.9-1.3-1.8-3.6-1.9-6.9h3.8c-.1 3.3-1 5.6-1.9 6.9zm2.6-1.3a15 15 0 0 0 1.3-5.6h3a8 8 0 0 1-4.3 5.6z"/></svg>
        <span>www.soundhaven-vorel.com</span>
      </li>
    </ul>
  </section>
</body>
</html>
```